Stationery Design Project for Nimbora, Chicago

Nimbora, a street parking application which helps car drivers find a street parking spot by offering an ideal path along which to look for parking. This path is calculated by our algorithm based on data (e.g. historical data, baseball games schedule, etc.). Along this path the driver will find a spot and will also save 70% of the search time. Customer we target is reg. between 21 and 45 yo.

We envision something young, fresh, bright and original. Slightly abstract maybe. It should represent the idea and elements of finding street parking in the city, e.g. car(s), parking spot, people, city, etc. (just ideas!).

Logo is attached.

Requirement:
- Business Cards (2 Sided Full Color CMYK)
- Letterhead (1 Sided Full Color CMYK)
- Envelope (1 Sided Full Color CMYK)
- Sticker (1 Sided Full Color CMYK), round with a 2inch diameter.

Reason: We're starting to get more and more designs and need more time to look into all of them. Very exciting!! Thanks to everybody!

Hi all, we're in the process of selecting our favs. Though choices!!! Really good submissions. Will keep you posted and sorry for the delay.

Target Market(s)

Car drivers and owners between 21 and 45

Industry/Entity Type

Parking

Requirements
Must have
• Sticker should be round and include company URL nimbora.com and the new logo which we will attach soon.
Should not have
• Should not be too serious or boring.

```html
<!DOCTYPE html>
<html lang="en">
<head>
<meta charset="utf-8">
<title>Nimbora – Business Card</title>
<link rel="stylesheet" href="https://fonts.googleapis.com/css2?family=Source+Sans+3:wght@400;600;700&display=swap">
<style>
  :root {
    --page-bg: #ece9e4;
    --card-bg: #ffffff;
    --brand-blue: #1f74bb;
    --brand-blue-faint: #d6e5f2;
    --ink: #2b2b2b;
    --ink-soft: #4a4a4a;
    --ring-grey: #d9d9d9;
    --ring-faint: #eeeeee;
    --asphalt: #8a8f95;
    --asphalt-light: #b9bdc1;
    --pavement: #d8d6d2;
  }
  * { box-sizing: border-box; margin: 0; padding: 0; }
  html, body { width: 1200px; height: 758px; overflow: hidden; }
  body {
    background: var(--page-bg);
    font-family: "Source Sans 3", Arial, sans-serif;
    color: var(--ink);
    position: relative;
  }
  .card {
    position: absolute;
    top: 224px;
    width: 540px;
    height: 310px;
    background: var(--card-bg);
    border-radius: 22px;
    box-shadow: 0 8px 24px rgba(0,0,0,0.18);
    overflow: hidden;
  }
  .card--front { left: 40px; }
  .card--back { left: 620px; }

  /* Front */
  .brand {
    position: absolute;
    left: 34px;
    top: 30px;
    display: flex;
    align-items: center;
    gap: 14px;
  }
  .brand__dot {
    width: 86px;
    height: 86px;
    border-radius: 50%;
    background: var(--brand-blue);
    box-shadow: 0 0 0 5px var(--card-bg), 0 0 0 7px var(--ring-grey);
  }
  .brand__name {
    font-size: 58px;
    font-weight: 700;
    color: var(--ink);
    letter-spacing: 0.5px;
    line-height: 1;
  }
  .front__decor {
    position: absolute;
    right: 34px;
    top: 112px;
    width: 150px;
    height: 150px;
    border-radius: 50%;
    background: var(--brand-blue-faint);
    box-shadow: 0 0 0 5px var(--card-bg), 0 0 0 7px var(--ring-faint);
  }
  .contact {
    position: absolute;
    left: 40px;
    top: 170px;
  }
  .contact__name {
    font-size: 19px;
    font-weight: 700;
    color: var(--brand-blue);
  }
  .contact__title {
    font-size: 15px;
    font-weight: 400;
    color: var(--ink-soft);
  }
  .contact__list {
    list-style: none;
    margin-top: 10px;
    font-size: 14px;
    line-height: 17px;
    color: var(--ink-soft);
  }
  .contact__list li { display: flex; align-items: center; gap: 6px; }
  .contact__icon { width: 11px; height: 11px; fill: var(--ink-soft); }
  .contact__address {
    margin-top: 8px;
    font-size: 14px;
    color: var(--ink-soft);
  }

  /* Back */
  .back__dot {
    position: absolute;
    left: 48px;
    top: 84px;
    width: 142px;
    height: 142px;
    border-radius: 50%;
    background: var(--brand-blue);
    box-shadow: 0 0 0 6px var(--card-bg), 0 0 0 9px var(--ring-grey);
  }
  .back__photo {
    position: absolute;
    right: 30px;
    top: 70px;
    width: 266px;
    height: 176px;
    border-radius: 4px;
    background:
      radial-gradient(ellipse at 55% 50%, rgba(255,255,255,0) 55%, rgba(255,255,255,0.85) 100%),
      linear-gradient(120deg, var(--pavement) 0%, var(--asphalt-light) 22%, var(--asphalt) 50%, var(--asphalt-light) 78%, var(--pavement) 100%);
  }
</style>
</head>
<body>
  <section class="card card--front" aria-label="Business card front">
    <div class="brand">
      <span class="brand__dot" aria-hidden="true"></span>
      <span class="brand__name">nimbora</span>
    </div>
    <div class="front__decor" aria-hidden="true"></div>
    <div class="contact">
      <p><span class="contact__name">Your Name,</span> <span class="contact__title">Title</span></p>
      <ul class="contact__list">
        <li>
          <svg class="contact__icon" viewBox="0 0 12 12" aria-hidden="true"><path d="M2.5 0.8 4.3 3 3.2 4.3c.7 1.6 1.9 2.8 3.5 3.5L8 6.7l2.2 1.8-.9 2.3C5 10.6 1.4 7 .2 1.7Z"/></svg>
          123-456-789
        </li>
        <li>
          <svg class="contact__icon" viewBox="0 0 12 12" aria-hidden="true"><rect x="3" y="0.5" width="6" height="11" rx="1"/><rect x="4" y="2" width="4" height="6" fill="#fff"/></svg>
          123-456-789
        </li>
        <li>
          <svg class="contact__icon" viewBox="0 0 12 12" aria-hidden="true"><rect x="0.5" y="2.5" width="11" height="7"/><path d="M0.8 2.8 6 6.6l5.2-3.8" fill="none" stroke="#fff" stroke-width="1"/></svg>
          info@nimbora.com
        </li>
        <li>
          <svg class="contact__icon" viewBox="0 0 12 12" aria-hidden="true"><circle cx="6" cy="6" r="5.5"/><path d="M0.5 6h11M6 0.5c-2.5 3-2.5 8 0 11M6 0.5c2.5 3 2.5 8 0 11" fill="none" stroke="#fff" stroke-width="0.8"/></svg>
          www.nimbora.com
        </li>
      </ul>
      <p class="contact__address">Complex name, Street name, City, State, zip code</p>
    </div>
  </section>

  <section class="card card--back" aria-label="Business card back">
    <span class="back__dot" aria-hidden="true"></span>
    <div class="back__photo" role="img" aria-label="Photo of cars parked in marked street bays, seen from above"></div>
  </section>
</body>
</html>
```